MRT Property - Business Cards

Looking for a business card & general letterhead, signage etc design for our new logo.

Colours:
000a20
0056a2
00b5ef
0088ce
68cef2

Fonts:
Poppins
Karla

Please keep look and feel of new brand - example in the zip package I sent.

```html
<!DOCTYPE html>
<html lang="en">
<head>
<meta charset="utf-8">
<title>MRT Property – Business Cards</title>
<link href="https://fonts.googleapis.com/css2?family=Poppins:wght@400;500;700&display=swap" rel="stylesheet">
<style>
  :root {
    --ink-navy: #0a0f1e;
    --brand-deep: #0056a2;
    --brand-mid: #0088ce;
    --brand-bright: #00b5ef;
    --brand-light: #68cef2;
    --paper: #ffffff;
    --stage: #e6e7ea;
  }
  * { box-sizing: border-box; margin: 0; padding: 0; }
  html, body {
    width: 1200px; height: 716px; overflow: hidden;
    background: var(--stage);
    font-family: "Poppins", sans-serif;
  }
  .canvas { position: relative; width: 1200px; height: 716px; }
  .card {
    position: absolute; top: 204px;
    width: 540px; height: 308px;
    background: var(--ink-navy);
    box-shadow: 0 10px 28px rgba(0,0,0,0.22);
    overflow: hidden;
  }
  .card--front { left: 40px; }
  .card--back { left: 620px; }

  .brand-feature {
    position: absolute;
    background: linear-gradient(135deg, var(--brand-light) 0%, var(--brand-bright) 45%, var(--brand-mid) 100%);
    opacity: 0.9;
  }
  .card--front .brand-feature {
    left: 320px; top: 120px; width: 220px; height: 188px;
    border-top-left-radius: 100% 100%;
  }
  .card--back .brand-feature {
    left: 0; top: 0; width: 250px; height: 170px;
    border-bottom-right-radius: 100% 100%;
  }

  .wordmark {
    color: var(--brand-deep);
    font-weight: 700;
    display: flex; align-items: center; gap: 10px;
    white-space: nowrap;
  }
  .wordmark__dot {
    width: 14px; height: 14px; border-radius: 50%;
    background: var(--brand-deep);
  }
  .card--front .wordmark {
    position: absolute; left: 40px; top: 30px; font-size: 28px;
  }
  .card--back .wordmark {
    position: absolute; right: 40px; top: 186px; font-size: 40px;
  }
  .card--back .wordmark__dot { width: 20px; height: 20px; }

  .person {
    position: absolute; left: 40px; top: 96px;
    padding-left: 14px;
    border-left: 6px solid var(--brand-deep);
  }
  .person__name {
    color: var(--brand-deep); font-weight: 700; font-size: 18px;
    line-height: 1.1; text-transform: uppercase;
  }
  .person__title { color: var(--paper); font-size: 12px; margin-top: 2px; }
  .address {
    position: absolute; left: 60px; top: 150px;
    color: var(--paper); font-size: 12px; line-height: 1.45;
  }
  .contacts {
    position: absolute; left: 40px; top: 200px;
    list-style: none; color: var(--paper); font-size: 12px; line-height: 1.7;
  }
  .contacts li { display: flex; align-items: center; gap: 8px; }
  .contacts svg { width: 11px; height: 11px; fill: var(--brand-bright); }
</style>
</head>
<body>
<main class="canvas">
  <section class="card card--front" aria-label="Business card front">
    <div class="brand-feature" role="img" aria-label="Large brand symbol decoration in light and mid blue"></div>
    <div class="wordmark"><span class="wordmark__dot"></span>MRT Property</div>
    <div class="person">
      <p class="person__name">Daniel Hart</p>
      <p class="person__title">Managing Director</p>
    </div>
    <p class="address">Your address, City<br>State, Zip 1234</p>
    <ul class="contacts">
      <li>
        <svg viewBox="0 0 24 24" aria-hidden="true"><path d="M6.6 10.8a15.1 15.1 0 0 0 6.6 6.6l2.2-2.2a1 1 0 0 1 1-.25 11.4 11.4 0 0 0 3.6.57 1 1 0 0 1 1 1V20a1 1 0 0 1-1 1A17 17 0 0 1 3 4a1 1 0 0 1 1-1h3.5a1 1 0 0 1 1 1c0 1.25.2 2.45.57 3.57a1 1 0 0 1-.25 1z"/></svg>
        123 456 789
      </li>
      <li>
        <svg viewBox="0 0 24 24" aria-hidden="true"><path d="M2 5h20v14H2z M4 7v.5l8 5 8-5V7l-8 5z"/></svg>
        info@yourgmail.com
      </li>
      <li>
        <svg viewBox="0 0 24 24" aria-hidden="true"><circle cx="12" cy="12" r="10"/></svg>
        www.yourwebsite.com
      </li>
    </ul>
  </section>

  <section class="card card--back" aria-label="Business card back">
    <div class="brand-feature" role="img" aria-label="Large brand symbol decoration in bright and mid blue"></div>
    <div class="wordmark"><span class="wordmark__dot"></span>MRT Property</div>
  </section>
</main>
</body>
</html>
```